i would like a business card to leave with customers and potential customers for electrical work and for the supply and install of reverse cycle airconditioning in the domestic and commercial market.
I own my own business and im a sole trader. I have an a'class electrical lisence and also a refrigeration lisence so i am
able to offer complete installations in airconditioning by a fully qualified and lisenced tradesman.
im looking for something that comes across as unique and professional.
i had the coluor black and some gold in mind but open to any coluors.
something like Lanterra Electrical & Refrigeration
or Lanterra Air.
i will use this design on a business card to advertise through summer to help generate installs through the busy season.

Target Market(s)

Mainly domestic house holds through summer who are in need of airconditioning and reliable information to acomadate thier cooling and heating requirements

Industry/Entity Type

Electrical

Requirements
Must have
• Business name- Lanterra
My name- Mark Delford
My mobile no- 0438 517 290
My email- mrdelford@qelvo.com.au
Installation & Decomissioning of aiconditioning split systems
LIC NO: TRK 540316
Nice to have
• Lanterra Electrical & Refrigeration

```html
<!DOCTYPE html>
<html lang="en">
<head>
<meta charset="utf-8">
<title>Lanterra Electrical – Business Card</title>
<link rel="stylesheet" href="https://fonts.googleapis.com/css2?family=Crimson+Text&family=Open+Sans:wght@300;400&display=swap">
<style>
  :root {
    --backdrop: #2f3b3c;
    --card-top: #2c2c2c;
    --card-bottom: #1c1c1c;
    --lime: #a6d13a;
    --lime-deep: #86c23f;
    --white: #ffffff;
    --label: #8a8a8a;
    --value: #cfcfcf;
    --name: #9b9b9b;
    --tagline: #dedede;
    --seal: #f4f4f4;
  }
  * { box-sizing: border-box; margin: 0; padding: 0; }
  html, body {
    width: 1200px; height: 900px; overflow: hidden;
    background: var(--backdrop);
  }
  .canvas { position: relative; width: 1200px; height: 900px; }
  .card {
    position: absolute; top: 133px; width: 436px; height: 714px;
    background: linear-gradient(180deg, var(--card-top), var(--card-bottom));
    box-shadow: 0 10px 30px rgba(0,0,0,0.55);
    overflow: hidden;
  }
  .card--front { left: 111px; }
  .card--back { left: 668px; }

  .brand {
    position: absolute; display: flex; align-items: center; gap: 14px;
    font-family: "Open Sans", sans-serif; font-weight: 400;
    color: var(--white); font-size: 44px;
  }
  .brand__dot {
    width: 34px; height: 34px; border-radius: 50%;
    background: var(--lime);
  }
  .card--front .brand { left: 0; right: 0; top: 325px; justify-content: center; }
  .card--back .brand { left: 40px; top: 128px; font-size: 40px; }

  .front__name {
    position: absolute; left: 8px; bottom: 10px;
    font-family: "Open Sans", sans-serif; font-weight: 300;
    font-size: 39px; letter-spacing: 2px; color: var(--white);
  }

  .holder {
    position: absolute; left: 305px; top: 30px; width: 300px;
    transform-origin: 0 0; transform: translate(100px, 0) rotate(90deg);
    font-family: "Crimson Text", serif; font-size: 50px;
    color: var(--name); white-space: nowrap; line-height: 1;
  }

  .contact {
    position: absolute; left: 23px; top: 355px; list-style: none;
    font-family: "Crimson Text", serif; font-size: 26px; line-height: 34px;
    color: var(--value);
  }
  .contact__label { color: var(--label); }

  .tagline {
    position: absolute; left: 17px; top: 527px;
    font-family: "Crimson Text", serif; font-size: 21px; line-height: 28px;
    color: var(--tagline);
  }

  .swoosh { position: absolute; left: 0; top: 0; }
  .seal {
    position: absolute; left: 364px; top: 637px; width: 59px; height: 66px;
    background: var(--seal);
  }
</style>
</head>
<body>
<main class="canvas">
  <section class="card card--front">
    <div class="brand"><span class="brand__dot"></span>Lanterra</div>
    <p class="front__name">Lanterra Electrical</p>
  </section>

  <section class="card card--back">
    <svg class="swoosh" width="436" height="714" viewBox="0 0 436 714" aria-hidden="true">
      <defs>
        <linearGradient id="floor" x1="0" y1="0" x2="1" y2="0">
          <stop offset="0" stop-color="#0c0c0c"/>
          <stop offset="0.55" stop-color="#2a2a2a"/>
          <stop offset="1" stop-color="#5a5a5a"/>
        </linearGradient>
      </defs>
      <path d="M0,650 Q300,632 436,505 L436,714 L0,714 Z" fill="url(#floor)"/>
      <path d="M0,646 Q300,628 436,500" fill="none" stroke="#000" stroke-width="6" transform="translate(0,6)"/>
      <path d="M0,642 Q300,624 436,496" fill="none" stroke="var(--lime)" stroke-width="9"/>
    </svg>

    <div class="brand"><span class="brand__dot"></span>Lanterra</div>
    <h1 class="holder">Mark Delford</h1>

    <ul class="contact">
      <li><span class="contact__label">mob:</span>&nbsp; 0438 517 290</li>
      <li><span class="contact__label">email:</span> mrdelford@qelvo.com.au</li>
      <li><span class="contact__label">LIC No:</span> TRK 540316</li>
    </ul>

    <p class="tagline">Installation &amp; Decomissioning of<br>airconditioning Split Systems</p>

    <div class="seal" role="img" aria-label="Authorised dealer badge"></div>
  </section>
</main>
</body>
</html>
```